Plakat für Foodtruck
Zielgruppe
Tom´s Frost Foodtruck, zielgruppe junges Publikum
Aufgabenstellung
Benötige ein Plakat von einem kleinen Menu in DinA1 und 20x110 cm
Format als PDF und Indesign, Design etwa so wie das Bild Kreidetafel siehe Anhang.
Stelle dir dein Softeis oder Frozen Yogurt zusammen
01. Softeis (Sorte Vanille) oder Frozen Yogurt
02. In der Waffel 4,00 €
03. Im Becher 5,00 €
04. Toppings zu je 0,50 €
04. Frische Früchte zu je 1,00 €
05. Soße zu je 0,50 €
Toppings
Brakol
Haselnusskronakt
Zip Lop
Marschmelows
Mini Kekse
Fimu
Schoko Chrispies
Schokoraspeln
Pluvinos
Waffelstücke
Zuckerstreusel bunt
Zuckerstreusel blau
Frische Früchte
je nach Saison
Soßen
Caramellsoße
Erdbeersoße
Mangosoße
Schokosoße
Pistaziensoße
Toffesoße

```html
<!DOCTYPE html>
<html lang="de">
<head>
<meta charset="utf-8">
<title>Tom´s Frost – Menü Plakat</title>
<link href="https://fonts.googleapis.com/css2?family=Titan+One&family=Inter:wght@300;400;500;700&display=swap" rel="stylesheet">
<style>
  :root {
    --page: #e3e3e3;
    --board: #2a2a2c;
    --board-light: #343437;
    --rose: #b8697a;
    --rose-faint: rgba(184,105,122,0.45);
    --chalk: #eeeeee;
    --chalk-soft: #dcdcdc;
  }
  * { margin: 0; padding: 0; box-sizing: border-box; }
  html, body { width: 890px; height: 1200px; overflow: hidden; background: var(--page); }
  body { position: relative; font-family: "Inter", sans-serif; color: var(--chalk); }

  .board {
    position: absolute;
    background: radial-gradient(ellipse at 40% 35%, var(--board-light), var(--board) 70%);
    overflow: hidden;
  }
  .poster { left: 41px; top: 36px; width: 561px; height: 792px; }
  .banner { left: 641px; top: 36px; width: 206px; height: 1129px; }

  .abs { position: absolute; white-space: nowrap; }
  .logo { position: absolute; }
  .logo-name {
    position: absolute; left: 0; right: 0; text-align: center;
    font-family: "Inter", sans-serif; font-weight: 700; color: var(--rose);
  }
  .headline {
    position: absolute; left: 0; right: 0; text-align: center;
    font-family: "Titan One", sans-serif; color: var(--rose); line-height: 1.3;
  }
  .price { font-family: "Titan One", sans-serif; color: var(--rose); }
  .row { position: absolute; display: flex; justify-content: space-between; }
  .section-title {
    position: absolute; font-family: "Titan One", sans-serif; color: var(--rose);
  }
  .section-number {
    position: absolute; font-family: "Titan One", sans-serif; color: var(--rose-faint);
  }
  .list span { margin-right: 11px; }
  .list { position: absolute; font-weight: 500; color: var(--chalk-soft); }
  .web { position: absolute; color: var(--rose); }
  .cone-art {
    position: absolute;
    background: linear-gradient(160deg, rgba(240,240,240,0.16), rgba(240,240,240,0.05));
    border-radius: 50% 50% 6px 6px / 60% 60% 6px 6px;
  }

  /* poster */
  .poster .logo { left: 180px; top: 37px; width: 200px; height: 200px; }
  .poster .logo-name { top: 82px; font-size: 30px; }
  .poster .headline { top: 253px; font-size: 24px; }
  .poster .intro { left: 180px; top: 340px; font-size: 16px; font-weight: 300; }
  .poster .row { left: 180px; width: 253px; font-size: 16.5px; font-weight: 500; }
  .poster .row.extra { width: 257px; }
  .poster .row .unit { font-weight: 300; }
  .poster .list { left: 180px; font-size: 12px; line-height: 15px; }
  .poster .cone-art { left: 379px; top: 597px; width: 140px; height: 195px; }

  /* banner */
  .banner .logo { left: 24px; top: 91px; width: 162px; height: 162px; }
  .banner .logo-name { top: 64px; font-size: 24px; }
  .banner .headline { top: 322px; font-size: 19px; line-height: 26.5px; }
  .banner .intro { left: 15px; top: 476px; font-size: 12.5px; font-weight: 300; line-height: 17px; }
  .banner .row { left: 15px; width: 177px; font-size: 13px; font-weight: 500; }
  .banner .row .unit { font-weight: 300; }
  .banner .list { left: 0; right: 0; text-align: center; font-size: 11px; line-height: 13.5px; white-space: normal; }
  .banner .cone-art { left: 59px; top: 999px; width: 82px; height: 130px; }
</style>
</head>
<body>

<section class="board poster">
  <div class="logo">
    <svg width="200" height="200" viewBox="0 0 200 200">
      <circle cx="100" cy="100" r="96" fill="none" stroke="var(--rose)" stroke-width="2"/>
    </svg>
    <div class="logo-name">Tom´s Frost</div>
  </div>

  <h1 class="headline">Stelle dir dein Softeis<br>oder Frozen Yogurt zusammen</h1>

  <p class="abs intro">Softeis (Sorte Vanille) oder Frozen Yogurt</p>

  <div class="row" style="top:380px"><span>In der Waffel</span><span class="price">4,00€</span></div>
  <div class="row" style="top:400px"><span>Im Becher</span><span class="price">5,00€</span></div>

  <div class="row extra" style="top:442px"><span>Toppings</span><span><span class="unit">zu je</span> <span class="price">0,50€</span></span></div>
  <div class="row extra" style="top:462px"><span>Frische Früchte</span><span><span class="unit">zu je</span> <span class="price">1,00€</span></span></div>
  <div class="row extra" style="top:483px"><span>Soße</span><span><span class="unit">zu je</span> <span class="price">0,50€</span></span></div>

  <div class="section-number" style="left:26px;top:518px;font-size:66px;">1</div>
  <h2 class="section-title" style="left:37px;top:536px;font-size:24px;">Toppings</h2>
  <p class="list" style="top:542px">
    <span>Brakol</span> <span>Haselnusskronakt</span> <span>Zip Lop</span> <span>Marschmelows</span><br>
    <span>Mini Kekse</span> <span>Fimu</span> <span>Schoko Chrispies</span> <span>Schokoraspeln</span> <span>Pluvinos</span><br>
    <span>Waffelstücke</span> <span>Zuckerstreusel bunt</span> <span>Zuckerstreusel blau</span><br>
    <span>Frische Früchte je nach Saison</span>
  </p>

  <div class="section-number" style="left:26px;top:598px;font-size:66px;">2</div>
  <h2 class="section-title" style="left:42px;top:618px;font-size:24px;">Soßen</h2>
  <p class="list" style="top:624px;line-height:14px;">
    <span>Caramellsoße</span> <span>Erdbeersoße</span> <span>Mangosoße</span><br>
    <span>Schokosoße</span> <span>Pistaziensoße</span> <span>Toffesoße</span>
  </p>

  <p class="web" style="left:221px;top:690px;font-size:13px;">www.tomsfrost.de</p>

  <div class="cone-art" role="img" aria-label="Kreidezeichnung einer Softeistüte"></div>
</section>

<section class="board banner">
  <div class="logo">
    <svg width="162" height="162" viewBox="0 0 162 162">
      <circle cx="81" cy="81" r="78" fill="none" stroke="var(--rose)" stroke-width="2"/>
    </svg>
    <div class="logo-name">Tom´s Frost</div>
  </div>

  <h1 class="headline">Stelle dir<br>dein Softeis<br>oder<br>Frozen Yogurt<br>zusammen</h1>

  <p class="abs intro">Softeis (Sorte Vanille)<br>oder Frozen Yogurt</p>

  <div class="row" style="top:526px"><span>In der Waffel</span><span class="price">4,00€</span></div>
  <div class="row" style="top:543px"><span>Im Becher</span><span class="price">5,00€</span></div>

  <div class="row" style="top:576px"><span>Toppings</span><span><span class="unit">zu je</span> <span class="price">0,50€</span></span></div>
  <div class="row" style="top:593px"><span>Frische Früchte</span><span><span class="unit">zu je</span> <span class="price">1,00€</span></span></div>
  <div class="row" style="top:609px"><span>Soße</span><span><span class="unit">zu je</span> <span class="price">0,50€</span></span></div>

  <div class="section-number" style="left:78px;top:655px;font-size:62px;">1</div>
  <h2 class="section-title" style="left:43px;top:678px;font-size:23px;">Toppings</h2>
  <p class="list" style="top:725px">
    Brakol&nbsp; Haselnusskronakt<br>Zip Lop&nbsp; Marschmelows<br>Mini Kekse&nbsp; Fimu<br>Schoko Chrispies<br>Schokoraspeln&nbsp; Pluvinos<br>Waffelstücke<br>Zuckerstreusel bunt<br>Zuckerstreusel blau<br>Frische Früchte je nach Saison
  </p>

  <div class="section-number" style="left:74px;top:871px;font-size:62px;">2</div>
  <h2 class="section-title" style="left:52px;top:896px;font-size:23px;">Soßen</h2>
  <p class="list" style="top:942px">
    Caramellsoße&nbsp; Erdbeersoße<br>Mangosoße&nbsp; Schokosoße<br>Pistaziensoße&nbsp; Toffesoße
  </p>

  <div class="cone-art" role="img" aria-label="Kreidezeichnung einer Softeistüte"></div>
</section>

</body>
</html>
```